Online business manager needs a website

I need a website designed and then coded. I am an online business manager serving a number of different industries providing administrative support to existing small businesses and helping solo practitioners get their new business up and running.

I didn't have a logo formally designed but have been using the attached avatar and wouldn't mind something that incorporated that.

The business doesn't have an official name, so I've just been using my name Lena Morvath, Online Business Manager or Lena Morvath, OBM. I've attached two documents that I have made previously for an example of content.

I would prefer the final site be in Wordpress.

Requirements
Must have
• A way to contact me, testimonials, list of services

```html
<!DOCTYPE html>
<html lang="en">
<head>
<meta charset="utf-8">
<title>Lena Morvath — Online Business Manager</title>
<link href="https://fonts.googleapis.com/css2?family=Playfair+Display:wght@500;600;700&family=Montserrat:wght@400;500;600;700&display=swap" rel="stylesheet">
<style>
:root{
  --purple:#5a4fc6;
  --purple-dark:#4a3fb3;
  --teal:#2bdbc9;
  --ink:#1f1f2e;
  --body:#4a4a5a;
  --muted:#8a8aa0;
  --pale:#eef1fb;
  --white:#ffffff;
  --serif:'Playfair Display', Georgia, serif;
  --sans:'Montserrat', Arial, sans-serif;
}
*{box-sizing:border-box;margin:0;padding:0}
html,body{width:1200px;height:3790px;overflow:hidden}
body{position:relative;font-family:var(--sans);color:var(--body);background:var(--white)}
.abs{position:absolute}
.section{position:absolute;left:0;width:1200px}
.serif{font-family:var(--serif)}
.btn{position:absolute;display:flex;align-items:center;justify-content:center;font-size:12px;font-weight:600;letter-spacing:.5px;border-radius:4px;text-transform:uppercase}
.btn-white{background:var(--white);color:var(--purple)}
.btn-outline{border:1.5px solid var(--white);color:var(--white)}
.btn-purple{background:var(--purple);color:var(--white)}
.placeholder{position:absolute;border-radius:6px}
.title{position:absolute;left:0;width:1200px;text-align:center;font-family:var(--serif);font-weight:600;font-size:34px;color:var(--purple)}
.title .accent{color:var(--teal)}
.arrow{position:absolute;width:24px;height:24px;border-radius:50%;display:flex;align-items:center;justify-content:center;font-size:13px}
.arrow-light{background:var(--white);color:var(--purple);box-shadow:0 2px 6px rgba(0,0,0,.12)}
.arrow-solid{background:#3b5bf0;color:var(--white)}

/* hero */
.hero{top:0;height:598px;background:linear-gradient(100deg,#5a4fc6 0%,#5a55c8 55%,#4aa4d2 85%,#2bdbc9 100%)}
.brand-name{font-family:var(--serif);font-size:28px;color:var(--white)}
.brand-sub{font-size:10px;font-weight:600;color:var(--white)}
.hero h1{position:absolute;left:92px;top:205px;font-family:var(--serif);font-weight:600;font-size:46px;line-height:60px;color:var(--white)}
.hero p{position:absolute;left:92px;top:390px;width:445px;font-size:11.5px;line-height:21.5px;color:var(--white)}
.growth-card{position:absolute;left:551px;top:195px;width:190px;height:140px;background:var(--white);border-radius:8px;box-shadow:0 8px 20px rgba(0,0,0,.15)}
.growth-card span{position:absolute;left:18px;top:26px;font-family:var(--serif);font-size:13px;color:var(--ink)}
.review-card{position:absolute;left:960px;top:468px;width:232px;height:86px;background:var(--white);border-radius:6px;box-shadow:0 6px 18px rgba(0,0,0,.15)}
.follow{position:absolute;left:1140px;top:330px;transform:rotate(-90deg);transform-origin:left top;font-size:11px;color:var(--white);letter-spacing:1px}

/* about */
.about{top:598px;height:537px}
.about h2{position:absolute;left:601px;top:120px;font-family:var(--serif);font-weight:600;font-size:34px;color:var(--purple)}
.about h2 .accent{color:var(--teal)}
.about p{position:absolute;left:601px;top:176px;width:506px;font-size:11.5px;line-height:22.7px;text-align:justify}

/* services */
.services{top:1135px;height:605px;background:var(--pale)}
.intro{position:absolute;left:250px;width:700px;text-align:center;font-size:11.5px;line-height:21px;color:var(--ink)}
.service-card{position:absolute;top:240px;width:245px;height:230px;background:var(--white);border-radius:12px;text-align:center;box-shadow:0 4px 16px rgba(90,79,198,.08)}
.service-card h3{margin-top:70px;font-family:var(--serif);font-size:16px;color:var(--ink)}
.service-card p{margin:14px 18px 0;font-size:10px;line-height:19px}
.service-icon{position:absolute;top:-48px;left:78px;width:90px;height:90px;border-radius:50%;display:flex;align-items:center;justify-content:center;border:5px solid var(--pale)}

/* industry */
.industry{top:1740px;height:292px}
.partner{position:absolute;top:126px;width:148px;height:94px;border:1px solid #e2e4ee;border-radius:4px;display:flex;align-items:center;justify-content:center;font-weight:700;font-size:17px;color:var(--ink);gap:8px}
.partner i{display:block;width:14px;height:14px;background:var(--purple);border-radius:50%}

/* testimonials */
.testimonials{top:2032px;height:471px;background:var(--pale)}
.quote{position:absolute;top:126px;width:445px;height:185px;background:var(--white);border-radius:6px;text-align:center;box-shadow:0 4px 16px rgba(0,0,0,.05)}
.quote .stars{margin-top:24px;color:#f4b31a;font-size:14px;letter-spacing:2px}
.quote p{margin:14px 28px 0;font-size:10px;font-style:italic;line-height:19px;color:var(--ink)}
.quote-side{position:absolute;top:126px;width:110px;height:185px;background:var(--white);border-radius:6px;opacity:.55;overflow:hidden;font-size:9px;font-style:italic;line-height:19px;color:var(--muted);padding-top:52px}
.avatar{position:absolute;top:278px;width:62px;height:62px;border-radius:50%;background:linear-gradient(135deg,#e6b9a0,#9b6b52);border:3px solid var(--white)}
.person{position:absolute;top:356px;width:445px;text-align:center}
.person b{display:block;font-family:var(--serif);font-size:15px;color:var(--ink)}
.person span{display:block;margin-top:6px;font-family:var(--serif);font-size:11px;color:#3b78d8}

/* work */
.work{top:2503px;height:522px}
.work-band{position:absolute;top:0;left:0;width:1200px;height:287px;background:linear-gradient(100deg,#5a4fc6 0%,#5a55c8 50%,#44b0d0 85%,#2bdbc9 100%)}
.work .title{color:var(--white);top:74px}

/* contact */
.contact-box{position:absolute;left:92px;top:3025px;width:1016px;height:500px;border-radius:16px;background:linear-gradient(100deg,#5a4fc6 0%,#5a55c8 45%,#3bbbd0 85%,#2bdbc9 100%)}
.contact-box h2{position:absolute;left:46px;top:112px;font-family:var(--serif);font-weight:600;font-size:32px;color:var(--white)}
.field{position:absolute;height:34px;background:var(--white);border-radius:3px;font-size:10px;color:var(--body);padding:11px 10px}

/* footer */
.footer h4{position:absolute;font-family:var(--serif);font-size:19px;font-weight:600;color:var(--purple)}
.footer h4 .accent{color:var(--teal)}
.f-icon{position:absolute;width:26px;height:26px;border-radius:50%;background:var(--purple);display:flex;align-items:center;justify-content:center}
.f-label{position:absolute;font-family:var(--serif);font-size:11px;color:var(--ink)}
.f-label b{display:block;font-size:12px}
</style>
</head>
<body>

<!-- HERO -->
<section class="section hero">
  <div class="placeholder" role="img" aria-label="Avatar of Lena Morvath at a laptop" style="left:122px;top:18px;width:80px;height:68px;background:linear-gradient(135deg,#f0d08a,#7fc7a0)"></div>
  <div class="abs brand-name" style="left:92px;top:86px">Lena Morvath</div>
  <div class="abs brand-sub" style="left:92px;top:122px">Online Business Manager</div>
  <div class="btn btn-white" style="left:980px;top:58px;width:128px;height:34px">Get Started</div>

  <h1>Start And Grow<br>Your New Business<br><u>Easily</u></h1>
  <p>Focused on the live event and entertainment industry. Helping artists and owners to better manage their career and business by strategically reviewing systems, recommending operational efficiencies, and managing inboxes.</p>
  <div class="btn btn-white" style="left:92px;top:475px;width:128px;height:35px">Get Started</div>
  <div class="btn btn-outline" style="left:238px;top:475px;width:128px;height:35px">Contact Us</div>

  <div class="placeholder" role="img" aria-label="Photo of Lena Morvath smiling on a laptop screen" style="left:580px;top:170px;width:530px;height:360px;background:linear-gradient(160deg,#d8b48a 0%,#c98d6c 45%,#4a4e5e 100%);border-radius:14px"></div>
  <div class="growth-card">
    <span>Growth</span>
    <svg class="abs" style="left:28px;top:58px" width="150" height="50" viewBox="0 0 150 50">
      <polyline points="0,40 20,26 38,34 56,18 74,28 96,10 116,20 140,4" fill="none" stroke="#2a2a3e" stroke-width="2"/>
      <circle cx="56" cy="18" r="3" fill="#3b5bf0"/>
    </svg>
  </div>
  <div class="review-card">
    <div class="abs serif" style="left:22px;top:14px;font-size:13px;font-weight:600;color:var(--ink)">12k Reviews On</div>
    <div class="abs" style="left:142px;top:12px;color:#f4b31a;font-size:12px;letter-spacing:1px">★★★★★</div>
    <svg class="abs" style="left:22px;top:42px" width="26" height="22" viewBox="0 0 26 22"><path d="M2 20 Q6 6 20 6" fill="none" stroke="var(--teal)" stroke-width="4"/><path d="M16 0 L26 6 L16 12 Z" fill="var(--teal)"/></svg>
    <div class="abs serif" style="left:56px;top:38px;font-size:24px;font-weight:600;color:var(--ink)">4.3</div>
    <div class="abs" style="left:115px;top:40px;width:26px;height:26px;border-radius:50%;background:#c99b7e;border:2px solid #fff"></div>
    <div class="abs" style="left:133px;top:40px;width:26px;height:26px;border-radius:50%;background:#a87560;border:2px solid #fff"></div>
    <div class="abs" style="left:151px;top:40px;width:26px;height:26px;border-radius:50%;background:#d6b096;border:2px solid #fff"></div>
    <div class="abs" style="left:169px;top:40px;width:28px;height:28px;border-radius:50%;background:#5a2a8a;border:2px solid #fff;color:#fff;font-size:9px;display:flex;align-items:center;justify-content:center">12k</div>
  </div>
  <div class="abs" style="left:1141px;top:170px;width:12px;height:12px;border-radius:2px;background:var(--white)"></div>
  <div class="abs" style="left:1141px;top:198px;width:12px;height:12px;border-radius:50%;background:var(--white)"></div>
  <div class="follow" style="top:326px">FOLLOW US ON</div>
  <div class="abs" style="left:1147px;top:336px;width:1px;height:60px;background:var(--white)"></div>
</section>

<!-- ABOUT -->
<section class="section about">
  <div class="placeholder" role="img" aria-label="Photo of a team meeting around a table" style="left:282px;top:70px;width:282px;height:220px;background:linear-gradient(135deg,#c7c1b8,#6c6a72)"></div>
  <div class="placeholder" role="img" aria-label="Photo of a smiling business team" style="left:77px;top:184px;width:283px;height:240px;background:linear-gradient(135deg,#e4e6ea,#3f4450);border:4px solid #fff"></div>
  <div class="placeholder" role="img" aria-label="Avatar illustration of Lena Morvath at a laptop" style="left:377px;top:307px;width:168px;height:160px;background:linear-gradient(135deg,#f8f8fb,#e3e8f2);box-shadow:0 4px 14px rgba(0,0,0,.08)"></div>
  <h2>About <span class="accent">Lena Morvath</span></h2>
  <p>Hi! I'm so excited that you have chosen to explore my portfolio. Helping businesses achieve their goals is my passion, and I'm thrilled that with my assistance you will have more time for your own passion project. I thrive while working independently, which means you can be confident when leaving tasks for me. The type of work that lights me up is anything involving organization and/or spreadsheets. You need data analyzed that includes multiple nested if formulas? You have an overwhelming amount of email to sort through and appointments to book? I'm your gal!</p>
  <div class="btn btn-purple" style="left:601px;top:352px;width:127px;height:34px">Contact Us</div>
</section>

<!-- SERVICES -->
<section class="section services">
  <div class="title" style="top:62px">Lena Morvath <span class="accent">Services</span></div>
  <div class="intro" style="top:124px">There are many variations of passages of Lorem Ipsum available, but the majority have suffered alteration in some form, by injected humour, or randomised words which don't look even slightly believable</div>
  <div class="arrow arrow-light" style="left:44px;top:320px">‹</div>
  <div class="arrow arrow-solid" style="left:1131px;top:320px">›</div>

  <div class="service-card" style="left:92px">
    <div class="service-icon" style="background:var(--purple)"><svg width="36" height="36" viewBox="0 0 36 36"><circle cx="18" cy="18" r="15" fill="none" stroke="#fff" stroke-width="2"/><path d="M10 18a8 8 0 0 1 14-5M26 18a8 8 0 0 1-14 5" fill="none" stroke="#fff" stroke-width="2"/></svg></div>
    <h3>Content Repurposing</h3>
    <p>It is a long established fact that a reader will be distracted by the readable content of a page when looking at its layout. The point of using Lorem Ipsum is that it has a more-or-less normal.</p>
  </div>
  <div class="service-card" style="left:348px">
    <div class="service-icon" style="background:var(--teal)"><svg width="36" height="36" viewBox="0 0 36 36"><rect x="6" y="20" width="5" height="10" fill="#fff"/><rect x="14" y="14" width="5" height="16" fill="#fff"/><rect x="22" y="8" width="5" height="22" fill="#fff"/><path d="M5 16 L14 9 L20 12 L30 4" fill="none" stroke="#fff" stroke-width="2"/></svg></div>
    <h3>Financial Analytics</h3>
    <p>It is a long established fact that a reader will be distracted by the readable content of a page when looking at its layout. The point of using Lorem Ipsum is that it has a more-or-less normal.</p>
  </div>
  <div class="service-card" style="left:605px">
    <div class="service-icon" style="background:var(--teal)"><svg width="36" height="36" viewBox="0 0 36 36"><rect x="5" y="6" width="26" height="18" rx="2" fill="none" stroke="#fff" stroke-width="2"/><rect x="9" y="10" width="18" height="10" fill="#fff" opacity=".6"/><rect x="12" y="27" width="12" height="3" fill="#fff"/></svg></div>
    <h3>Data Entry</h3>
    <p>It is a long established fact that a reader will be distracted by the readable content of a page when looking at its layout. The point of using Lorem Ipsum is that it has a more-or-less normal.</p>
  </div>
  <div class="service-card" style="left:862px">
    <div class="service-icon" style="background:var(--purple)"><svg width="36" height="36" viewBox="0 0 36 36"><rect x="5" y="5" width="10" height="10" fill="none" stroke="#fff" stroke-width="2"/><circle cx="26" cy="10" r="5" fill="none" stroke="#fff" stroke-width="2"/><path d="M8 30 L22 16" stroke="#fff" stroke-width="2"/></svg></div>
    <h3>Graphic Creations</h3>
    <p>It is a long established fact that a reader will be distracted by the readable content of a page when looking at its layout. The point of using Lorem Ipsum is that it has a more-or-less normal.</p>
  </div>
  <div class="btn btn-purple" style="left:550px;top:498px;width:127px;height:34px">Contact Us</div>
</section>

<!-- INDUSTRY -->
<section class="section industry">
  <div class="title" style="top:60px;color:var(--teal)">Industry <span style="color:var(--purple)">Lena Serve</span></div>
  <div class="arrow arrow-light" style="left:44px;top:161px">‹</div>
  <div class="arrow arrow-solid" style="left:1131px;top:161px">›</div>
  <div class="partner" style="left:92px"><i></i>Harborline</div>
  <div class="partner" style="left:265px">Deltaric</div>
  <div class="partner" style="left:439px"><i></i>Lumea Stays</div>
  <div class="partner" style="left:612px">Corvix</div>
  <div class="partner" style="left:786px">Norvale</div>
  <div class="partner" style="left:959px">Tellspan</div>
</section>

<!-- TESTIMONIALS -->
<section class="section testimonials">
  <div class="title" style="top:60px">What Client's Say <span class="accent">About Lena</span></div>
  <div class="quote-side" style="left:0;text-align:right;padding-right:8px">time than I had, stepped up thorough and would highly</div>
  <div class="quote-side" style="left:1088px;text-align:left;padding-left:30px">"When it became stepped up timely; able to</div>
  <div class="arrow arrow-light" style="left:44px;top:208px">‹</div>
  <div class="arrow arrow-solid" style="left:1131px;top:208px">›</div>

  <div class="quote" style="left:141px">
    <div class="stars">★★★★★</div>
    <p>"When it became apparent that a project would take more time than I had, Lena stepped up to take on the required research. She was thorough and timely; able to meet a last-minute 12-hour deadline. I would highly recommend Lena to assist with your next project."</p>
  </div>
  <div class="avatar" role="img" aria-label="Client portrait" style="left:332px"></div>
  <div class="person" style="left:141px"><b>Dana R.</b><span>Owner, Brightside Roofing</span></div>

  <div class="quote" style="left:614px">
    <div class="stars">★★★★★</div>
    <p>"When it became apparent that a project would take more time than I had, Lena stepped up to take on the required research. She was thorough and timely; able to meet a last-minute 12-hour deadline. I would highly recommend Lena to assist with your next project."</p>
  </div>
  <div class="avatar" role="img" aria-label="Client portrait" style="left:805px"></div>
  <div class="person" style="left:614px"><b>Dana R.</b><span>Owner, Brightside Roofing</span></div>
</section>

<!-- WORK -->
<section class="section work">
  <div class="work-band"></div>
  <div class="title">Lena Morvath Work</div>
  <div class="arrow arrow-light" style="left:44px;top:278px">‹</div>
  <div class="arrow arrow-solid" style="left:1131px;top:278px">›</div>
  <div class="placeholder" role="img" aria-label="Podcast cover artwork about business workflows and automations" style="left:92px;top:127px;width:324px;height:323px;background:linear-gradient(135deg,#fbe9e0,#f3c9b8);border-radius:10px"></div>
  <div class="placeholder" role="img" aria-label="Podcast episode artwork on mindful body movement" style="left:438px;top:127px;width:324px;height:323px;background:linear-gradient(135deg,#f7f3ef,#e8ddd6);border:5px solid #2b2c6e;border-radius:10px"></div>
  <div class="placeholder" role="img" aria-label="Podcast episode artwork with a desk, keyboard and headphones" style="left:784px;top:127px;width:324px;height:323px;background:linear-gradient(135deg,#f2d3d8,#e6b8c1);border-radius:10px"></div>
</section>

<!-- CONTACT -->
<div class="contact-box">
  <h2>Get In Touch With Lena Morvath</h2>
  <div class="field" style="left:46px;top:170px;width:226px">First Name*</div>
  <div class="field" style="left:292px;top:170px;width:222px">Last Name*</div>
  <div class="field" style="left:46px;top:219px;width:226px">Phone Number*</div>
  <div class="field" style="left:292px;top:219px;width:222px">Email*</div>
  <div class="field" style="left:46px;top:267px;width:468px;height:68px">Message*</div>
  <div class="btn btn-white" style="left:46px;top:368px;width:126px;height:34px">Submit</div>
  <div class="placeholder" role="img" aria-label="Illustrated avatar of Lena Morvath waving from a laptop" style="left:558px;top:65px;width:420px;height:370px;background:linear-gradient(160deg,#f3d58e 0%,#8fcfa6 55%,#9aa0a8 100%);border-radius:14px"></div>
</div>

<!-- FOOTER -->
<footer class="section footer" style="top:3560px;height:230px">
  <h4 style="left:92px;top:10px">Contact <span class="accent">Us</span></h4>
  <div class="f-icon" style="left:92px;top:58px"><svg width="12" height="12" viewBox="0 0 12 12"><path d="M2 1 L4 1 L5 4 L3.5 5 Q5 8 7 8.5 L8 7 L11 8 L11 10 Q10 11 9 11 Q1 10 1 2 Q1 1 2 1Z" fill="#fff"/></svg></div>
  <div class="f-label" style="left:130px;top:56px"><b>Call Us</b>555.210.4478</div>
  <div class="f-icon" style="left:92px;top:108px"><svg width="12" height="10" viewBox="0 0 12 10"><rect x="0.5" y="0.5" width="11" height="9" fill="none" stroke="#fff"/><path d="M0.5 0.5 L6 5 L11.5 0.5" fill="none" stroke="#fff"/></svg></div>
  <div class="f-label" style="left:130px;top:104px"><b>Email</b>hello@lenamorvath.example</div>

  <div class="placeholder" role="img" aria-label="Avatar logo of Lena Morvath" style="left:565px;top:20px;width:120px;height:88px;background:linear-gradient(135deg,#f0d08a,#7fc7a0)"></div>
  <div class="abs serif" style="left:0;width:1260px;text-align:center;top:108px;font-size:28px;color:var(--ink)">Lena Morvath</div>
  <div class="abs" style="left:0;width:1260px;text-align:center;top:146px;font-size:10px;font-weight:600;color:var(--purple)">Online Business Manager</div>

  <h4 style="left:985px;top:10px">Follow <span class="accent">Us On</span></h4>
  <div class="f-icon" style="left:985px;top:58px"></div>
  <div class="f-label" style="left:1023px;top:64px">Friendpage</div>
  <div class="f-icon" style="left:985px;top:106px"></div>
  <div class="f-label" style="left:1023px;top:112px">Worklink</div>

  <div class="abs" style="left:92px;top:185px;width:1016px;height:1px;background:#dfe1ea"></div>
  <div class="abs" style="left:0;width:1200px;text-align:center;top:205px;font-size:10px;color:var(--ink)">© 2023 Lena Morvath. All Rights Reserved.</div>
</footer>

</body>
</html>
```